New Business Card Design for Manufacturing

We are an engineering/manufacturing company that offers Advanced machining/assembly/engineering services, as well as innovative products for the heavy duty engine cooling markets.

We are looking to get a new business card designed that is clean and modern looking, but still fits the wide range of technical/skilled work we do.

- We hope to use this design as the base for other design work in new Presentations, web, and print work.

Industry/Entity Type

Engineering

Contact Information for Business Card

Our preferred color of blue is (RGB) 22/71/159 but can vary slightly from that color. Our content will be our Logo and full company name (Vantrell Forge Works, Inc.), company address, name, job title, phone number with extension, cell number, fax number, website, and email address on the cards.
We'd like the full company name next to the logo, but we are open to other interpretations of that layout.
Preferably, we would like the back side to be clean with just our logo, and the front to contain all of the contact information.

Colors
2f74b4
0355a3
85abd2

Requirements
Must have
• - Logo, company name, needed content - We are open to interpretation beyond that.
• - Standard size business card.
• - Horizontal orientation.
• - Enough space for lengthy names / job titles (for example, a job title could read "Directory of Human Resources" or "V.P. of Governmental Affairs"). We need this to look clean, whether the title be short (CEO) or long (as described above).

```html
<!DOCTYPE html>
<html lang="en">
<head>
<meta charset="utf-8">
<title>Vantrell Forge Works – Business Card</title>
<link rel="stylesheet" href="https://fonts.googleapis.com/css2?family=Open+Sans:wght@400;600;800&display=swap">
<style>
  :root {
    --blue-deep: #0b4fa0;
    --blue-sky: #4db3e6;
    --ink: #4a4a4a;
    --teal-link: #0e5e8c;
    --paper: #ffffff;
    --backdrop: #e9ebee;
  }
  * { margin: 0; padding: 0; box-sizing: border-box; }
  html, body {
    width: 1200px; height: 1000px; overflow: hidden;
    background: var(--backdrop);
    font-family: "Open Sans", Arial, sans-serif;
  }
  .canvas { position: relative; width: 1200px; height: 1000px; }
  .card {
    position: absolute; width: 760px; height: 434px;
    background: var(--paper); overflow: hidden;
    box-shadow: 0 10px 30px rgba(0,0,0,.18);
  }
  .card-front { left: 110px; top: 48px; }
  .card-back { left: 330px; top: 516px; }
  .card-shapes { position: absolute; inset: 0; }

  .company-name {
    position: absolute; left: 34px; top: 46px;
    color: var(--paper); font-weight: 800; font-size: 23px;
    line-height: 1.05; text-transform: uppercase; letter-spacing: .2px;
  }
  .company-name small { font-size: 10px; }
  .holder { position: absolute; left: 345px; top: 100px; color: var(--paper); }
  .holder-name { font-size: 29px; font-weight: 400; letter-spacing: 1px; }
  .holder-title { font-size: 15px; letter-spacing: 1.2px; text-transform: uppercase; margin-top: 2px; }

  .address-strip {
    position: absolute; left: 300px; top: 228px; width: 420px; height: 40px;
    background: linear-gradient(to bottom, rgba(0,0,0,.08), rgba(0,0,0,0) 70%);
    border-radius: 50% 50% 0 0 / 20px 20px 0 0;
  }
  .contact {
    position: absolute; display: flex; flex-direction: column; gap: 8px;
    color: var(--ink); font-size: 15px; letter-spacing: 1px; text-transform: uppercase;
  }
  .contact li { list-style: none; display: flex; align-items: center; gap: 12px; }
  .contact svg { width: 16px; height: 16px; fill: var(--ink); flex: none; }
  .contact-address { left: 318px; top: 244px; }
  .contact-online { left: 452px; top: 310px; gap: 4px; }
  .contact-phones { left: 60px; top: 340px; gap: 4px; }

  .brand-mark {
    position: absolute; left: 215px; width: 360px; top: 178px;
    text-align: center; white-space: nowrap;
    color: var(--blue-deep); font-weight: 800; font-size: 30px; letter-spacing: .3px;
  }
  .site-url {
    position: absolute; right: 150px; bottom: 56px;
    color: var(--teal-link); font-size: 19px;
  }
</style>
</head>
<body>
<main class="canvas">

  <section class="card card-front" aria-label="Business card front">
    <svg class="card-shapes" viewBox="0 0 760 434" aria-hidden="true">
      <path fill="var(--blue-sky)" d="M0 0 H760 V200 H330 C300 200 292 225 282 255 C272 285 245 300 210 300 H0 Z"/>
      <path fill="var(--blue-deep)" d="M0 0 H248 C244 110 238 210 185 255 C162 274 130 282 90 282 H0 Z"/>
    </svg>

    <h1 class="company-name">Vantrell<br>Forge<br>Works <small>Inc</small></h1>

    <div class="holder">
      <p class="holder-name">NAME OF CEO</p>
      <p class="holder-title">Directory of Human Resources</p>
    </div>

    <div class="address-strip"></div>
    <ul class="contact contact-address">
      <li><svg viewBox="0 0 16 16"><path d="M8 1a5 5 0 0 0-5 5c0 4 5 9 5 9s5-5 5-9a5 5 0 0 0-5-5zm0 7a2 2 0 1 1 0-4 2 2 0 0 1 0 4z"/></svg>Your company address</li>
    </ul>

    <ul class="contact contact-online">
      <li><svg viewBox="0 0 16 16"><path d="M8 1a7 7 0 1 0 0 14A7 7 0 0 0 8 1zm5 6h-2.6a11 11 0 0 0-1-4A5.5 5.5 0 0 1 13 7zM8 2.6c.7.9 1.2 2.6 1.3 4.4H6.7C6.8 5.2 7.3 3.5 8 2.6zM6.6 3a11 11 0 0 0-1 4H3a5.5 5.5 0 0 1 3.6-4zM3 9h2.6a11 11 0 0 0 1 4A5.5 5.5 0 0 1 3 9zm5 4.4c-.7-.9-1.2-2.6-1.3-4.4h2.6c-.1 1.8-.6 3.5-1.3 4.4zM9.4 13a11 11 0 0 0 1-4H13a5.5 5.5 0 0 1-3.6 4z"/></svg>Website</li>
      <li><svg viewBox="0 0 16 16"><path d="M1 3h14v2L8 9 1 5zm0 4 7 4 7-4v6H1z"/></svg>Email address</li>
    </ul>

    <ul class="contact contact-phones">
      <li><svg viewBox="0 0 16 16"><path d="M1 5c0-2 3-3 7-3s7 1 7 3v1h-3V5H4v1H1zm3 2h8l2 7H2zm4 1.5a2 2 0 1 0 0 4 2 2 0 0 0 0-4z"/></svg>Phone number</li>
      <li><svg viewBox="0 0 16 16"><path d="M3 1h3l1 4-2 1c1 2 3 4 5 5l1-2 4 1v3c0 1-1 2-2 2C7 15 1 9 1 3c0-1 1-2 2-2z"/></svg>Cell number</li>
      <li><svg viewBox="0 0 16 16"><path d="M4 1h8v4H4zM1 6h14v6h-3v3H4v-3H1zm4 4v4h6v-4z"/></svg>Fax number</li>
    </ul>
  </section>

  <section class="card card-back" aria-label="Business card back">
    <svg class="card-shapes" viewBox="0 0 760 434" aria-hidden="true">
      <path fill="var(--blue-deep)" d="M0 140 H130 C175 140 200 165 205 215 H0 Z"/>
      <path fill="var(--blue-sky)" d="M0 215 H205 V250 C205 290 178 312 135 312 H0 Z"/>
      <path fill="var(--blue-deep)" d="M760 70 H640 C605 70 585 92 585 125 V150 H760 Z"/>
      <path fill="var(--blue-sky)" d="M585 150 H760 V270 H690 C628 270 585 228 585 185 Z"/>
    </svg>
    <p class="brand-mark">Vantrell Forge Works</p>
    <p class="site-url">www.vantrellforge.com</p>
  </section>

</main>
</body>
</html>
```